limo company looking for a graphic business card with professional look and feel

Looking for a business card design that can give you the full picture of the limo company by looking at the card - we provide airport service, wedding, birthday, night out, etc... we have sedans, suvs , limos, and party buses. I want the business card to have a professional look because we are targetting corporate clients as well as regular retail.
Info about the business can be found at: http://brevlink.example/Qm4Tz7
Target Market(s)
corporate clients and retail
Industry/Entity Type
Business
Contact Information for Business Card
I would like the logo and the name of the company to be in raised print - not sure if design makes a difference for that or just print - I need it designed in 350dpi
Requirements
Must have
- pictures of vehicle types (sedans, suvs, limos, party bus). pictures of interior of the limos if possible. list service types (weddings, birthdays, proms, airport transportation) & service areas (houston, the woodlands, spring, tomball, cypress, kingwood).
Nice to have
- nice professional look to it.

```html
<!DOCTYPE html>
<html lang="en">
<head>
<meta charset="utf-8">
<title>Velvet Line &amp; Transportation – Business Card</title>
<link rel="stylesheet" href="https://fonts.googleapis.com/css2?family=Marcellus+SC&display=swap">
<style>
  :root {
    --page-bg: #f0f0f0;
    --card-bg: #3b3a3a;
    --card-edge: #2c2c2c;
    --rule: #ffffff;
    --text-light: #ffffff;
    --text-muted: #d6d6d6;
    --text-dark: #2b2b2b;
  }
  * { box-sizing: border-box; margin: 0; padding: 0; }
  html, body { width: 1020px; height: 1200px; overflow: hidden; }
  body {
    background: var(--page-bg);
    position: relative;
    font-family: "Marcellus SC", serif;
  }
  .card {
    position: absolute;
    left: 39px;
    width: 894px;
    background: var(--card-bg);
    box-shadow: 0 0 0 2px var(--card-edge);
    overflow: hidden;
  }
  .card--front { top: 59px; height: 521px; }
  .card--back  { top: 618px; height: 517px; }
  .card__frame {
    position: absolute;
    inset: 13px;
    border: 4px solid var(--rule);
  }

  /* Front */
  .brand {
    position: absolute;
    left: 48px;
    top: 62px;
    width: 230px;
    color: var(--text-light);
    text-align: center;
  }
  .brand__name { font-size: 34px; letter-spacing: 1px; line-height: 1; }
  .brand__sub { font-size: 17px; margin-top: 6px; letter-spacing: 0.5px; }
  .services {
    position: absolute;
    left: 48px;
    top: 168px;
    width: 230px;
    list-style: none;
    text-align: center;
    color: var(--text-muted);
    font-size: 15px;
    letter-spacing: 1.5px;
    line-height: 30px;
  }
  .contact {
    position: absolute;
    left: 38px;
    bottom: 44px;
    width: 250px;
    text-align: center;
    color: var(--text-light);
    font-size: 14px;
    letter-spacing: 0.5px;
  }
  .pillar {
    position: absolute;
    width: 15px;
    bottom: 17px;
    background: var(--rule);
  }
  .pillar--one { left: 319px; top: 202px; }
  .pillar--two { left: 360px; top: 230px; }
  .pillar--three { left: 401px; top: 202px; }
  .gallery__photo {
    position: absolute;
    border: 3px solid var(--rule);
  }
  .photo--door { left: 553px; top: 17px; width: 158px; height: 151px;
    background: linear-gradient(135deg, #e8e8e8, #6d6d6d 60%, #2a2a2a); }
  .photo--suit { left: 714px; top: 17px; width: 163px; height: 151px;
    background: linear-gradient(160deg, #3a3a3a, #0f0f10); }
  .photo--toast { left: 553px; top: 171px; width: 158px; height: 151px;
    background: radial-gradient(circle at 45% 40%, #c9b98a, #5a5240 55%, #1d1c18); }
  .photo--lights { left: 714px; top: 171px; width: 163px; height: 151px;
    background: radial-gradient(circle at 40% 75%, #d0507a, #5a2a6a 35%, #141018 70%); }
  .photo--cabin { left: 553px; top: 325px; width: 324px; height: 179px;
    background: linear-gradient(180deg, #4a5fa8, #1c2566 50%, #0b0f2a); }

  /* Back */
  .areas {
    position: absolute;
    left: 56px;
    top: 152px;
    width: 200px;
    list-style: none;
    text-align: center;
    color: var(--text-light);
    font-size: 21px;
    letter-spacing: 2px;
    line-height: 43px;
  }
  .fleet-rail {
    position: absolute;
    bottom: 17px;
    border-left: 13px solid var(--rule);
    border-top: 16px solid var(--rule);
  }
  .fleet-rail--bus { left: 315px; top: 98px; width: 362px; }
  .fleet-rail--suv { left: 347px; top: 139px; width: 465px; }
  .fleet-rail--sedan { left: 386px; top: 182px; width: 491px; }
  .fleet-label {
    position: absolute;
    color: var(--text-dark);
    font-size: 17px;
    letter-spacing: 3px;
    line-height: 16px;
  }
  .fleet-label--bus { left: 356px; top: 98px; }
  .fleet-label--suv { left: 377px; top: 139px; }
  .fleet-label--limo { left: 521px; top: 139px; }
  .fleet-label--sedan { left: 460px; top: 182px; }
  .cityscape {
    position: absolute;
    left: 401px;
    top: 206px;
    width: 476px;
    height: 294px;
    background: radial-gradient(ellipse at 55% 45%, #8a6a3a, #3a2c1c 45%, #111010 85%);
  }
</style>
</head>
<body>
  <section class="card card--front">
    <div class="card__frame"></div>
    <div class="brand">
      <div class="brand__name">Velvet Line</div>
      <div class="brand__sub">&amp; Transportation</div>
    </div>
    <ul class="services">
      <li>Weddings</li>
      <li>Birthdays</li>
      <li>Proms</li>
      <li>Nights Out</li>
      <li>Airport Service</li>
    </ul>
    <div class="contact">brevlink.example/Qm4Tz7</div>
    <div class="pillar pillar--one"></div>
    <div class="pillar pillar--two"></div>
    <div class="pillar pillar--three"></div>
    <div class="gallery__photo photo--door" role="img" aria-label="Photo of an open white limousine door"></div>
    <div class="gallery__photo photo--suit" role="img" aria-label="Photo of a chauffeur in a black suit"></div>
    <div class="gallery__photo photo--toast" role="img" aria-label="Photo of champagne glasses raised in a toast"></div>
    <div class="gallery__photo photo--lights" role="img" aria-label="Photo of colourful party lights"></div>
    <div class="gallery__photo photo--cabin" role="img" aria-label="Photo of a party bus interior with blue lighting"></div>
  </section>

  <section class="card card--back">
    <div class="card__frame"></div>
    <ul class="areas">
      <li>Houston</li>
      <li>The Woodland</li>
      <li>Spring</li>
      <li>Tomball</li>
      <li>Cypress</li>
      <li>Kingwood</li>
    </ul>
    <div class="fleet-rail fleet-rail--bus"></div>
    <div class="fleet-rail fleet-rail--suv"></div>
    <div class="fleet-rail fleet-rail--sedan"></div>
    <span class="fleet-label fleet-label--bus">Party Bus</span>
    <span class="fleet-label fleet-label--suv">SUVS</span>
    <span class="fleet-label fleet-label--limo">Limo</span>
    <span class="fleet-label fleet-label--sedan">Sedans</span>
    <div class="cityscape" role="img" aria-label="Aerial night photo of city lights and highways"></div>
  </section>
</body>
</html>
```